Harbourline Physiotherapy business card design

We need a fresh, new business card design for our physiotherapy clinic Harbourline Physiotherapy

Will attach logo soon we had logo designed from our last project

Industry/Entity Type

Physical Therapy

Contact Information for Business Card

On front
Needs our logo, contact details:
58 Wexley Lane Larkspur Vale NSW 2795
Ph/f: 02 9481 2057
info@harbourlinephysio.example.com.au

Requirements
Must have
• On the back of the card needs to have area to write down follow up appointments
• On front
• Needs our logo
• The colours have to be the colours in our logo which are: sky blue, black and white
• Font to be same as our logo please
• We want the card to look simple, not too cluttered but to the point
Should not have
• We don't need any extra pictures other than our logo

```html
<!DOCTYPE html>
<html lang="en">
<head>
<meta charset="utf-8">
<title>Harbourline Physiotherapy – Business Card</title>
<link href="https://fonts.googleapis.com/css2?family=Open+Sans:wght@400;600;700&display=swap" rel="stylesheet">
<style>
  :root {
    --backdrop: #e9e7e3;
    --card-white: #ffffff;
    --card-grey: #eceef0;
    --brand-blue: #1f5fbf;
    --brand-blue-deep: #1c2f8f;
    --brand-blue-light: #2a8fd8;
    --arc-grey: #5b5e63;
    --ink-blue: #2a6fc9;
    --dot-blue: #6d9bd8;
    --text-white: #ffffff;
  }
  * { box-sizing: border-box; margin: 0; padding: 0; }
  html, body { width: 1200px; height: 843px; overflow: hidden; }
  body {
    background: var(--backdrop);
    font-family: "Open Sans", Arial, sans-serif;
    position: relative;
  }
  .card {
    position: absolute;
    width: 520px;
    height: 318px;
    border-radius: 18px;
    overflow: hidden;
    box-shadow: 0 10px 26px rgba(0,0,0,0.22);
  }

  /* Back: appointment card */
  .card-back {
    left: 50px; top: 262px;
    background: linear-gradient(180deg, var(--card-white) 0%, var(--card-white) 70%, var(--card-grey) 100%);
    padding: 34px 34px 0;
    color: var(--ink-blue);
  }
  .appointment-title {
    text-align: center;
    font-weight: 700;
    font-size: 20px;
    margin-bottom: 24px;
  }
  .field-row { display: flex; gap: 18px; margin-bottom: 20px; font-size: 15px; }
  .field { display: flex; align-items: flex-end; flex: 1; }
  .field-label { white-space: nowrap; margin-right: 6px; }
  .field-line { flex: 1; border-bottom: 2px dotted var(--dot-blue); height: 16px; }
  .field-suffix { font-size: 11px; margin-left: 4px; }
  .field-time { flex: 0.8; }
  .blank-line { border-bottom: 2px dotted var(--dot-blue); height: 16px; margin: -4px 0 12px; }
  .cancel-note { text-align: center; font-size: 10.5px; font-weight: 600; line-height: 1.45; }

  /* Front: contact card */
  .card-front { left: 630px; top: 262px; background: var(--card-white); }
  .card-front svg.face { position: absolute; inset: 0; }
  .contact { position: absolute; left: 30px; color: var(--text-white); }
  .contact-name { top: 30px; }
  .contact-name .person { font-weight: 700; font-size: 21px; line-height: 1.2; }
  .contact-name .role { font-size: 14px; }
  .contact-details { top: 150px; font-size: 13px; line-height: 1.45; white-space: nowrap; }
  .contact-details .address { margin-bottom: 16px; }
  .contact-details b { font-weight: 700; }
  .brand {
    position: absolute;
    left: 336px; top: 126px;
    display: flex; align-items: center; gap: 8px;
    color: var(--brand-blue);
    font-weight: 700;
    font-size: 18px;
    line-height: 1.15;
  }
  .brand-dot { width: 20px; height: 20px; border-radius: 50%; background: var(--brand-blue); flex: none; }
</style>
</head>
<body>

<section class="card card-back" aria-label="Appointment card back">
  <h2 class="appointment-title">Next Appointment</h2>
  <div class="field-row">
    <div class="field"><span class="field-label">Name :</span><span class="field-line"></span></div>
    <div class="field field-time"><span class="field-label">Time :</span><span class="field-line"></span><span class="field-suffix">AM/PM</span></div>
  </div>
  <div class="field-row">
    <div class="field"><span class="field-label">Date :</span><span class="field-line"></span></div>
  </div>
  <div class="field-row">
    <div class="field"><span class="field-label">Note :</span><span class="field-line"></span></div>
  </div>
  <div class="blank-line"></div>
  <div class="blank-line"></div>
  <p class="cancel-note">Please give me 24 hours notice if you need to change your appointment or<br>a cancellation fee may apply.</p>
</section>

<section class="card card-front" aria-label="Business card front">
  <svg class="face" width="520" height="318" viewBox="0 0 520 318" aria-hidden="true">
    <defs>
      <radialGradient id="blueField" cx="0.3" cy="0.4" r="0.75">
        <stop offset="0" stop-color="#2a8fd8"/>
        <stop offset="0.55" stop-color="#1f5fbf"/>
        <stop offset="1" stop-color="#1c2f8f"/>
      </radialGradient>
      <linearGradient id="whiteField" x1="0" y1="0" x2="0" y2="1">
        <stop offset="0" stop-color="#ffffff"/>
        <stop offset="1" stop-color="#e6e8ea"/>
      </linearGradient>
    </defs>
    <rect width="520" height="318" fill="url(#whiteField)"/>
    <path d="M0 0 H322 C282 70 276 200 345 318 H0 Z" fill="url(#blueField)"/>
    <path d="M322 0 C282 70 276 200 345 318" fill="none" stroke="#5b5e63" stroke-width="9"/>
    <path d="M334 0 C296 70 290 200 358 318" fill="none" stroke="#ffffff" stroke-width="5"/>
  </svg>

  <div class="contact contact-name">
    <p class="person">Daniel Reeve</p>
    <p class="role">CEO/Founder</p>
  </div>
  <div class="contact contact-details">
    <p class="address">58 Wexley Lane Larkspur Vale<br>NSW 2795</p>
    <p><b>Ph/Fax</b> 02 9481 2057</p>
    <p>info@harbourlinephysio.example.com.au</p>
    <p>www.harbourlinephysio.example.com.au</p>
  </div>

  <div class="brand">
    <span class="brand-dot"></span>
    <span class="brand-name">Harbourline<br>Physiotherapy</span>
  </div>
</section>

</body>
</html>
```